Brewlark Cup Society - A Monthly Subscription Coffee Club - Shopify Website Design

A monthly subscription company. Need a Shopify Website Design and uploaded to fully work with Tidal Renewals.

Please look at these sites for examples as well as the images I enclosed.

https://www.sipvantor.com/
https://mokrate.com/
https://www.platewinder.com/
https://www.globunchies.com/

Number of Pages Required

1 page

```html
<!DOCTYPE html>
<html lang="en">
<head>
<meta charset="utf-8">
<title>Brewlark Cup Society – Speciality Coffee Subscription</title>
<link href="https://fonts.googleapis.com/css2?family=Oswald:wght@500;600&family=Lato:wght@400;700&display=swap" rel="stylesheet">
<style>
:root{
  --blue:#1d5a8b;
  --blue-dark:#174a74;
  --blue-deep:#123c5f;
  --tan:#d9a36b;
  --tan-dark:#c98d52;
  --ink:#1f2a36;
  --muted:#7c8490;
  --line:#e3e6ea;
  --white:#ffffff;
}
*{margin:0;padding:0;box-sizing:border-box}
html,body{width:1200px;height:4156px;overflow:hidden}
body{font-family:"Lato",Arial,sans-serif;color:var(--ink);background:var(--white);position:relative}
.display{font-family:"Oswald","Arial Narrow",sans-serif;text-transform:uppercase;letter-spacing:.5px}
.btn{display:inline-block;font-family:"Lato",Arial,sans-serif;font-weight:700;font-size:13px;letter-spacing:1px;text-transform:uppercase;padding:13px 26px;border-radius:3px;background:var(--tan);color:var(--white);text-decoration:none}
.photo{border-radius:4px}

/* header + hero */
.hero{position:absolute;top:0;left:0;width:1200px;height:580px;background:linear-gradient(180deg,var(--blue) 0%,var(--blue-dark) 100%)}
.nav{position:absolute;top:22px;left:120px;right:120px;height:56px;display:flex;align-items:center;justify-content:space-between}
.brand{display:flex;align-items:center;gap:10px;font-family:"Oswald","Arial Narrow",sans-serif;font-weight:600;font-size:22px;color:var(--white);text-transform:uppercase;letter-spacing:1px;white-space:nowrap}
.brand-dot{width:14px;height:14px;border-radius:50%;background:var(--white);flex:none}
.menu{display:flex;align-items:center;gap:26px;font-size:15px;color:var(--white)}
.menu a{color:var(--white);text-decoration:none}
.menu .buy{border:1px solid var(--white);padding:6px 14px;border-radius:3px;font-size:13px;font-weight:700}
.hero-copy{position:absolute;top:118px;left:120px;width:680px;color:var(--white)}
.eyebrow{font-family:"Oswald","Arial Narrow",sans-serif;font-size:17px;font-weight:500;letter-spacing:1px;text-transform:uppercase}
.hero-title{font-size:44px;line-height:54px;font-weight:600;margin:16px 0 34px}
.hero-photo{position:absolute;top:80px;left:760px;width:380px;height:440px;background:radial-gradient(ellipse at 55% 55%,#c59a74 0%,#8e6445 45%,rgba(29,90,139,0) 75%)}
.band{position:absolute;top:580px;left:0;width:1200px;height:52px;background:var(--tan);display:flex;align-items:center;justify-content:center;gap:22px;color:var(--white);font-size:15px}
.band .btn{background:var(--blue-deep);padding:9px 16px;font-size:12px}

/* intro */
.intro{position:absolute;top:632px;left:0;width:1200px;height:248px;text-align:center}
.section-title{font-size:30px;font-weight:600;color:var(--ink)}
.intro .section-title{margin-top:84px}
.intro p{width:560px;margin:18px auto 0;font-size:15px;line-height:24px;color:var(--muted)}

/* features */
.feature{position:absolute;left:0;width:1200px;height:345px}
.feature .photo{position:absolute}
.feature-text{position:absolute;width:440px}
.feature-text h3{font-size:20px;font-weight:600;color:var(--blue-deep);margin-bottom:14px}
.feature-text p{font-size:14px;line-height:23px;color:var(--muted)}
.feature.right-text .feature-text{text-align:right}

.divider{position:absolute;top:2262px;left:120px;width:960px;height:1px;background:var(--line)}

/* sign up */
.signup{position:absolute;top:2263px;left:0;width:1200px;height:537px}
.signup-copy{position:absolute;top:68px;left:120px;width:480px}
.signup-copy h2{font-size:24px;font-weight:600;color:var(--blue-deep)}
.signup-copy .lead{margin-top:14px;font-size:14px;line-height:22px;color:var(--tan-dark)}
.checklist{list-style:none;margin-top:18px}
.checklist li{display:flex;align-items:center;gap:10px;font-size:14px;color:var(--muted);margin-bottom:11px}
.checklist svg{flex:none}
.signup-copy .note{font-size:12px;color:var(--muted);margin:8px 0 28px}
.signup .photo{position:absolute;top:36px;left:700px;width:400px;height:430px;background:radial-gradient(ellipse at 50% 55%,#d8b48a 0%,#c69767 45%,rgba(255,255,255,0) 74%)}

/* charity */
.charity{position:absolute;top:2800px;left:0;width:1200px;height:360px;background:var(--blue);color:var(--white)}
.charity-copy{position:absolute;top:52px;left:120px;width:580px}
.charity-copy h2{font-size:24px;font-weight:600;white-space:nowrap}
.charity-copy p{margin-top:12px;font-size:13px;line-height:21px;opacity:.9}
.aims{display:grid;grid-template-columns:1fr 1fr;gap:16px 24px;margin-top:24px;font-size:13px}
.aims div{display:flex;align-items:center;gap:12px}
.aims .ico{width:34px;height:34px;border-radius:50%;background:var(--blue-dark);flex:none}
.charity .photo{position:absolute;top:40px;left:740px;width:360px;height:280px;background:linear-gradient(90deg,#3b2a4a 0%,#6a4a32 35%,#b8895a 62%,#e8e2d6 100%);border-radius:6px}

/* instagram */
.insta{position:absolute;top:3160px;left:0;width:1200px;height:620px}
.insta .section-title{position:absolute;top:100px;width:1200px;text-align:center}
.grid{position:absolute;top:160px;left:120px;width:960px;display:grid;grid-template-columns:repeat(6,1fr);gap:8px}
.grid div{height:196px}

/* footer */
.footer{position:absolute;top:3780px;left:0;width:1200px;height:340px;background:var(--blue);color:var(--white)}
.footer .brand{position:absolute;top:70px;left:120px;font-size:18px}
.social{position:absolute;top:112px;left:120px;display:flex;gap:8px}
.social span{width:24px;height:24px;border-radius:50%;border:1px solid var(--white)}
.f-col{position:absolute;top:66px}
.f-col h4{font-family:"Oswald","Arial Narrow",sans-serif;font-weight:500;font-size:18px;margin-bottom:16px}
.f-col p{font-size:14px;line-height:22px;opacity:.9}
.f-contact{left:420px;width:240px}
.f-news{left:740px;width:340px}
.subscribe{display:flex;align-items:center;gap:14px;margin-top:20px}
.subscribe .field{flex:1;border-bottom:1px solid rgba(255,255,255,.6);padding:8px 0;font-size:13px;opacity:.8}
.subscribe .btn{background:transparent;border:1px solid var(--white);padding:9px 14px;font-size:12px}
.legal{position:absolute;top:4120px;left:0;width:1200px;height:36px;background:var(--blue-deep);color:var(--white);font-size:12px;display:flex;align-items:center;justify-content:center;opacity:.95}
</style>
</head>
<body>

<header class="hero">
  <nav class="nav">
    <div class="brand"><span class="brand-dot"></span>Brewlark Cup Society</div>
    <div class="menu">
      <a>Subscribe</a><a>Gift</a><a>Giving Back</a><a>Blog</a><a>About Us</a><a>Contact</a>
      <svg width="16" height="16" viewBox="0 0 16 16" fill="none" stroke="#fff" stroke-width="2"><circle cx="7" cy="7" r="5"/><path d="M11 11l4 4"/></svg>
      <svg width="18" height="16" viewBox="0 0 18 16" fill="none" stroke="#fff" stroke-width="1.6"><path d="M1 1h3l2 9h9l2-6H5"/><circle cx="7" cy="14" r="1.2"/><circle cx="14" cy="14" r="1.2"/></svg>
      <a class="buy">BUY</a>
    </div>
  </nav>
  <div class="hero-copy">
    <div class="eyebrow">Feel good coffee subscription</div>
    <h1 class="hero-title display">Speciality coffee &amp; delicious<br>treats delivered to your door</h1>
    <a class="btn">Get started</a>
  </div>
  <div class="hero-photo photo" role="img" aria-label="Open gift box of coffee bags and treats"></div>
</header>

<div class="band">Giving back to the communities that bring you exceptional coffee <a class="btn">Get involved</a></div>

<section class="intro">
  <h2 class="section-title display">A coffee subscription like no other</h2>
  <p>Lorem ipsum dolor sit amet, consectetur adipiscing elit, sed do eiusmod tempor incididunt ut labore et dolore magna aliqua. Quis ipsum suspendisse ultrices gravida.</p>
</section>

<section class="feature" style="top:880px">
  <div class="photo" role="img" aria-label="Black and white coffee pouches" style="left:180px;top:20px;width:320px;height:330px;background:linear-gradient(90deg,#2a2a2a 0%,#3a3a3a 45%,#e8e6e2 55%,#f4f3f0 100%)"></div>
  <div class="feature-text" style="left:580px;top:96px">
    <h3 class="display">The finest coffee</h3>
    <p>Lorem ipsum dolor sit amet, consectetur adipiscing elit, sed do eiusmod tempor incididunt ut labore et dolore magna a. Quis ipsum suspendisse ultrices gravida. Risus commodo viverra maecenas accumsan lacus vel facilisis.</p>
  </div>
</section>

<section class="feature right-text" style="top:1225px">
  <div class="feature-text" style="left:360px;top:70px">
    <h3 class="display">Better than fair trade</h3>
    <p>Lorem ipsum dolor sit amet, consectetur adipiscing elit, sed do eiusmod tempor incididunt ut labore et dolore magna a. Quis ipsum suspendisse ultrices gravida. Risus commodo viverra maecenas accumsan lacus vel facilisis.</p>
  </div>
  <div class="photo" role="img" aria-label="Sack of spilled coffee beans" style="left:830px;top:40px;width:300px;height:230px;background:radial-gradient(ellipse at 50% 50%,#a88a62 0%,#6b4a2e 40%,rgba(255,255,255,0) 72%)"></div>
</section>

<section class="feature" style="top:1560px">
  <div class="photo" role="img" aria-label="Kraft paper coffee bags" style="left:160px;top:0;width:360px;height:320px;background:radial-gradient(ellipse at 50% 50%,#e7c9a4 0%,#d8b088 45%,rgba(255,255,255,0) 74%)"></div>
  <div class="feature-text" style="left:580px;top:112px">
    <h3 class="display">Accompanied by delectable treats</h3>
    <p>Lorem ipsum dolor sit amet, consectetur adipiscing elit, sed do eiusmod tempor incididunt ut labore et dolore magna a. Quis ipsum suspendisse ultrices gravida. Risus commodo viverra maecenas accumsan lacus vel facilisis.</p>
  </div>
</section>

<section class="feature right-text" style="top:1880px">
  <div class="feature-text" style="left:360px;top:130px">
    <h3 class="display">For the ultimate ‘feel good’ subscription</h3>
    <p>Lorem ipsum dolor sit amet, consectetur adipiscing elit, sed do eiusmod tempor incididunt ut labore et dolore magna a. Quis ipsum suspendisse ultrices gravida. Risus commodo viverra maecenas accumsan lacus vel facilisis.</p>
  </div>
  <div class="photo" role="img" aria-label="Opened shipping box with coffee" style="left:840px;top:20px;width:290px;height:350px;background:radial-gradient(ellipse at 50% 50%,#d2a477 0%,#c08e5d 45%,rgba(255,255,255,0) 74%)"></div>
</section>

<div class="divider"></div>

<section class="signup">
  <div class="signup-copy">
    <h2 class="display">Sign up for your monthly subscription</h2>
    <p class="lead">Each month, a fresh box from Brewlark Cup Society lands at your door with the following delivered inside:</p>
    <ul class="checklist">
      <li><svg width="14" height="14" viewBox="0 0 14 14"><rect x=".5" y=".5" width="13" height="13" fill="none" stroke="#d9a36b"/><path d="M3 7l3 3 5-6" fill="none" stroke="#d9a36b" stroke-width="1.6"/></svg>Lorem ipsum dolor sit amet, consectetur adipiscing</li>
      <li><svg width="14" height="14" viewBox="0 0 14 14"><rect x=".5" y=".5" width="13" height="13" fill="none" stroke="#d9a36b"/><path d="M3 7l3 3 5-6" fill="none" stroke="#d9a36b" stroke-width="1.6"/></svg>Lorem ipsum dolor sit amet, consectetur adipiscing</li>
      <li><svg width="14" height="14" viewBox="0 0 14 14"><rect x=".5" y=".5" width="13" height="13" fill="none" stroke="#d9a36b"/><path d="M3 7l3 3 5-6" fill="none" stroke="#d9a36b" stroke-width="1.6"/></svg>Lorem ipsum dolor sit amet, consectetur adipiscing</li>
      <li><svg width="14" height="14" viewBox="0 0 14 14"><rect x=".5" y=".5" width="13" height="13" fill="none" stroke="#d9a36b"/><path d="M3 7l3 3 5-6" fill="none" stroke="#d9a36b" stroke-width="1.6"/></svg>Lorem ipsum dolor sit amet, consectetur adipiscing</li>
    </ul>
    <p class="note">Free shipping on all subscriptions, cancel at any time.</p>
    <a class="btn">Subscribe today</a>
  </div>
  <div class="photo" role="img" aria-label="Subscription box with coffee bags and treats"></div>
</section>

<section class="charity">
  <div class="charity-copy">
    <h2 class="display">Working alongside charities around the world</h2>
    <p>Lorem ipsum dolor sit amet, consectetur adipiscing elit, sed do eiusmod tempor incididunt ut labore et dolore magna aliqua. Quis ipsum suspendisse ultrices gravida commodo viverra maecenas accumsan lacus vel facilisis. Lorem ipsum dolor sit amet, consectetur adipiscing elit.</p>
    <div class="aims">
      <div><span class="ico"></span>Provision of water filters</div>
      <div><span class="ico"></span>Sponsoring school children</div>
      <div><span class="ico"></span>Helping in farmland efforts</div>
      <div><span class="ico"></span>Promoting sustainable farming</div>
    </div>
  </div>
  <div class="photo" role="img" aria-label="Row of retail coffee bags"></div>
</section>

<section class="insta">
  <h2 class="section-title display">Follow on Instagram</h2>
  <div class="grid">
    <div class="photo" role="img" aria-label="Coffee bags on a table" style="background:linear-gradient(135deg,#c9d6cf,#8aa79a)"></div>
    <div class="photo" role="img" aria-label="Latte from above" style="background:linear-gradient(135deg,#d8c2a4,#7a5637)"></div>
    <div class="photo" role="img" aria-label="Hands holding coffee beans" style="background:linear-gradient(135deg,#8a5a3a,#3e2414)"></div>
    <div class="photo" role="img" aria-label="Coffee cups on a counter" style="background:linear-gradient(135deg,#e6dccd,#a88868)"></div>
    <div class="photo" role="img" aria-label="Cafe interior" style="background:linear-gradient(135deg,#b07a4a,#4a2a18)"></div>
    <div class="photo" role="img" aria-label="Barista pouring coffee" style="background:linear-gradient(135deg,#6a4a3a,#201410)"></div>
    <div class="photo" role="img" aria-label="Coffee cup and beans" style="background:linear-gradient(135deg,#d8cfc2,#7b6046)"></div>
    <div class="photo" role="img" aria-label="Roasted coffee beans" style="background:linear-gradient(135deg,#5a3420,#2a160c)"></div>
    <div class="photo" role="img" aria-label="Bowl of coffee beans" style="background:linear-gradient(135deg,#9a6a44,#3a2214)"></div>
    <div class="photo" role="img" aria-label="Takeaway cup in hand" style="background:linear-gradient(135deg,#e4ddd2,#b89878)"></div>
    <div class="photo" role="img" aria-label="Coffee harvest" style="background:linear-gradient(135deg,#7a4a2a,#c48a5a)"></div>
    <div class="photo" role="img" aria-label="Flat lay of coffee tools" style="background:linear-gradient(135deg,#c8a88a,#6a4a34)"></div>
  </div>
</section>

<footer class="footer">
  <div class="brand"><span class="brand-dot"></span>Brewlark Cup Society</div>
  <div class="social"><span></span><span></span><span></span><span></span></div>
  <div class="f-col f-contact">
    <h4>Contact</h4>
    <p>123 Avenue name, City name<br>00000 United States</p>
    <p style="margin-top:14px">(000) 000 0000</p>
  </div>
  <div class="f-col f-news">
    <h4>Calling All Coffee Lovers!</h4>
    <p>Sign up to be the first to find out all of the latest news from Brewlark Cup Society and never miss a thing!</p>
    <div class="subscribe"><span class="field">Email Address</span><a class="btn">Subscribe</a></div>
  </div>
</footer>
<div class="legal">Brewlark Cup Society © 2020 All Rights Reserved | Privacy Policy</div>

</body>
</html>
```